Looking for someone to design a business card for my plumbing business Quandor Plumbing Solutions I want the background also to be black, must attract clients. If possible I want the front to be the logo and the back to show maybe the details.

Target Market(s)

Clients

Industry/Entity Type

Plumbing maintenance

Contact Information for Business Card

Name: Felix, Contact: 0461 539 207, Email: quandorplumbingsolutions@mailbrook.example, Licence number 728093K

Font styles to use
Other font styles liked:
• as per logo maybe?

Colors

Designer to choose colors to be used in the design.

Requirements
Nice to have
• stating the service I provide, emergency plumbing, plumbing maintenance, drainage maintenance, block sewer and stormwater, camera and locating.

```html
<!DOCTYPE html>
<html lang="en">
<head>
<meta charset="utf-8">
<title>Quandor Plumbing Solutions – Business Card</title>
<link rel="stylesheet" href="https://fonts.googleapis.com/css2?family=Figtree:wght@400;700&display=swap">
<style>
  :root {
    --page: #141414;
    --card: #232323;
    --blue: #4a90cc;
    --white: #f2f2f2;
    --text: #e6e6e6;
    --ghost: #363636;
    --font: "Figtree", "Helvetica Neue", Arial, sans-serif;
  }
  html, body {
    margin: 0;
    padding: 0;
    width: 1200px;
    height: 1059px;
    overflow: hidden;
    background: var(--page);
    font-family: var(--font);
  }
  .card {
    position: absolute;
    left: 255px;
    width: 690px;
    height: 392px;
    background: var(--card);
    border-radius: 20px;
    overflow: hidden;
  }
  .card--front { top: 90px; }
  .card--back { top: 548px; }

  /* Front */
  .brand {
    position: absolute;
    left: 40px;
    top: 150px;
    width: 270px;
    display: flex;
    align-items: center;
    gap: 14px;
  }
  .brand__dot {
    flex: none;
    width: 22px;
    height: 22px;
    border-radius: 50%;
    background: var(--blue);
  }
  .brand__name {
    margin: 0;
    font-weight: 700;
    font-size: 30px;
    line-height: 1.05;
    color: var(--white);
  }
  .brand__name small {
    display: block;
    font-size: 16px;
    letter-spacing: 0.5px;
    margin-top: 4px;
  }
  .divider {
    position: absolute;
    left: 334px;
    top: 129px;
    width: 2px;
    height: 134px;
    background: var(--blue);
  }
  .person {
    position: absolute;
    left: 359px;
    top: 126px;
  }
  .person__name {
    margin: 0;
    font-weight: 700;
    font-size: 27px;
    line-height: 1;
    color: var(--blue);
    letter-spacing: 0.5px;
  }
  .person__role {
    margin: 4px 0 0;
    font-size: 16px;
    color: var(--text);
  }
  .contacts {
    position: absolute;
    left: 359px;
    top: 193px;
    margin: 0;
    padding: 0;
    list-style: none;
    color: var(--text);
    font-size: 16px;
  }
  .contacts li {
    display: flex;
    align-items: center;
    gap: 8px;
    height: 26px;
  }
  .contacts svg { width: 13px; height: 13px; flex: none; }
  .contacts .contacts__email { font-size: 13.5px; }
  .wave {
    position: absolute;
    left: 0;
    top: 0;
  }
  .licence {
    position: absolute;
    right: 46px;
    top: 356px;
    margin: 0;
    font-size: 15.5px;
    color: var(--white);
  }

  /* Back */
  .ghost-brand {
    position: absolute;
    left: 0;
    right: 0;
    top: 110px;
    margin: 0;
    text-align: center;
    font-weight: 700;
    font-size: 46px;
    line-height: 1;
    color: var(--ghost);
  }
  .ghost-brand small {
    display: block;
    font-size: 22px;
    letter-spacing: 1px;
    margin-top: 8px;
  }
  .services {
    position: absolute;
    left: 0;
    right: 0;
    top: 310px;
    margin: 0;
    text-align: center;
    font-size: 16px;
    line-height: 27px;
    color: var(--text);
  }
  .services .sep { color: var(--blue); margin: 0 7px; }
</style>
</head>
<body>

<section class="card card--front" aria-label="Business card front">
  <div class="brand">
    <span class="brand__dot" aria-hidden="true"></span>
    <p class="brand__name">Quandor<small>Plumbing Solutions</small></p>
  </div>

  <div class="divider"></div>

  <div class="person">
    <p class="person__name">FELIX</p>
    <p class="person__role">Founder &amp; CEO</p>
  </div>

  <ul class="contacts">
    <li>
      <svg viewBox="0 0 24 24" aria-hidden="true"><path fill="#4a90cc" d="M6.6 10.8a15 15 0 0 0 6.6 6.6l2.2-2.2a1 1 0 0 1 1-.25 11.4 11.4 0 0 0 3.6.6 1 1 0 0 1 1 1V20a1 1 0 0 1-1 1A17 17 0 0 1 3 4a1 1 0 0 1 1-1h3.5a1 1 0 0 1 1 1c0 1.25.2 2.45.6 3.6a1 1 0 0 1-.25 1z"/></svg>
      <span>0461 539 207</span>
    </li>
    <li>
      <svg viewBox="0 0 24 24" aria-hidden="true"><path fill="#4a90cc" d="M2 5h20v14H2z"/><path fill="none" stroke="#232323" stroke-width="1.8" d="M2 5l10 8 10-8"/></svg>
      <span class="contacts__email">quandorplumbingsolutions@mailbrook.example</span>
    </li>
    <li>
      <svg viewBox="0 0 24 24" aria-hidden="true"><circle cx="12" cy="12" r="11" fill="#4a90cc"/></svg>
      <span>@QuandorPlumbingSolutions</span>
    </li>
  </ul>

  <svg class="wave" width="690" height="392" viewBox="0 0 690 392" aria-hidden="true">
    <path fill="#f2f2f2" d="M250 364 C380 350 500 322 580 320 C630 319 670 328 690 337 L690 351 C670 339 630 329 580 329 C500 331 380 352 250 364 Z"/>
    <path fill="#4a90cc" d="M0 322 C80 362 200 368 300 364 C420 358 520 334 580 335 C630 336 670 345 690 356 L690 392 L0 392 Z"/>
  </svg>

  <p class="licence">Licence number 728093K</p>
</section>

<section class="card card--back" aria-label="Business card back">
  <p class="ghost-brand">Quandor<small>PLUMBING SOLUTIONS</small></p>
  <p class="services">
    Emergency plumbing<span class="sep">•</span>Plumbing maintenance<span class="sep">•</span>Drainage maintenance<br>
    Block sewer and stormwater<span class="sep">•</span>Camera and locating
  </p>
</section>

</body>
</html>
```